Super elegant, crisp & clean Business card design required

We recently upgraded our branding - which is on our website - talvendoraphoto.com

I would like a simple, yet elegant, clean business card design please.

The font of my logo is Cinzel - and because of the natural colour - it's best to have this on a black background.

I would like to have the back of the business card - with simply my logo.

PLEASE DO NOT SUBMIT A COMPLICATED / UNCLEAN DESIGN

Industry/Entity Type

Business

Contact Information for Business Card

Talven Doroshko Photography

Font styles to use
Other font styles liked:
• Cinzel

Requirements
Must have
• A backpage with nothing but my logo
• Simple design - stands out
Should not have
• Colour that dont align with my logo
• Over complicated '/ non symmetrical design

```html
<!DOCTYPE html>
<html lang="en">
<head>
<meta charset="utf-8">
<title>Talven Doroshko Photography – Business Card</title>
<link href="https://fonts.googleapis.com/css2?family=Cinzel:wght@400;600;700&display=swap" rel="stylesheet">
<style>
  :root {
    --stage: #2b2523;
    --card-black: #050505;
    --card-glow: #262626;
    --gold: #a8997a;
    --gold-deep: #8c7d5f;
    --white: #f4f2ee;
    --edge-light: #d9d9d9;
  }
  * { margin: 0; padding: 0; box-sizing: border-box; }
  html, body {
    width: 1200px;
    height: 844px;
    overflow: hidden;
    background: var(--stage);
  }
  .stage {
    position: relative;
    width: 1200px;
    height: 844px;
    display: flex;
    align-items: center;
    justify-content: center;
    gap: 60px;
  }
  .card {
    position: relative;
    width: 520px;
    height: 297px;
    background: var(--card-black);
    overflow: hidden;
    box-shadow: 0 10px 26px rgba(0,0,0,.55);
    font-family: "Cinzel", serif;
  }

  /* Front side */
  .card-front::before,
  .card-front::after {
    content: "";
    position: absolute;
    top: 0;
    bottom: 0;
    width: 22px;
    background: var(--gold);
  }
  .card-front::before { left: 0; }
  .card-front::after { right: 0; }
  .contact {
    position: absolute;
    inset: 0 22px;
    display: flex;
    flex-direction: column;
    align-items: center;
    justify-content: center;
    text-align: center;
    color: var(--white);
  }
  .person-name {
    font-size: 18px;
    font-weight: 600;
    color: var(--gold);
    letter-spacing: .5px;
    padding-bottom: 3px;
    border-bottom: 1px solid var(--gold-deep);
  }
  .person-role {
    font-size: 12px;
    font-weight: 700;
    margin-top: 3px;
    letter-spacing: .5px;
  }
  .contact-group {
    margin-top: 20px;
    font-size: 15px;
    font-weight: 600;
    line-height: 1.15;
  }
  .contact-group.web { margin-top: 16px; font-size: 13px; }
  .address {
    margin-top: 18px;
    font-size: 13px;
    font-weight: 600;
  }

  /* Back side */
  .card-back {
    background: radial-gradient(ellipse at 45% 40%, var(--card-glow) 0%, var(--card-black) 70%);
  }
  .edge-tab {
    position: absolute;
    width: 22px;
    height: 36px;
    background: var(--gold);
  }
  .edge-tab.left { left: 0; top: 160px; border-right: 3px solid var(--edge-light); }
  .edge-tab.right { right: 0; top: 12px; border-left: 3px solid var(--edge-light); }
  .brand {
    position: absolute;
    inset: 0;
    display: flex;
    flex-direction: column;
    align-items: center;
    justify-content: center;
    color: var(--gold);
    font-weight: 400;
    text-align: center;
  }
  .brand-mark {
    width: 14px;
    height: 14px;
    background: var(--gold);
    margin-bottom: 18px;
  }
  .brand-name {
    font-size: 26px;
    letter-spacing: 1px;
    line-height: 1.2;
  }
  .brand-name .sub {
    display: block;
    font-size: 11px;
    letter-spacing: 7px;
  }
</style>
</head>
<body>
<main class="stage">
  <section class="card card-front" aria-label="Business card front">
    <div class="contact">
      <p class="person-name">Elias Marwood</p>
      <p class="person-role">Managing Director</p>
      <div class="contact-group">
        <p>044-456-7890</p>
        <p>123-456-7890</p>
      </div>
      <div class="contact-group web">
        <p>infoname@yourwebsite.com</p>
        <p>www.talvendoraphoto.com</p>
      </div>
      <p class="address">1234 Address Tag Line | Country Name, AB | 123456</p>
    </div>
  </section>

  <section class="card card-back" aria-label="Business card back">
    <span class="edge-tab left"></span>
    <span class="edge-tab right"></span>
    <div class="brand">
      <span class="brand-mark"></span>
      <p class="brand-name">Talven Doroshko<span class="sub">Photography</span></p>
    </div>
  </section>
</main>
</body>
</html>
```